Business Card Design

I already have a company logo for my company. I have a logo for the manufacturer we represent. I want a professional business card design.

```html
<!DOCTYPE html>
<html lang="en">
<head>
<meta charset="utf-8">
<title>Beacon Alert Group — Business Card</title>
<link href="https://fonts.googleapis.com/css2?family=Open+Sans:wght@400;700&display=swap" rel="stylesheet">
<style>
  :root {
    --stage: #3b3b3b;
    --stage-dark: #1c1c1c;
    --card: #141414;
    --red: #e3222b;
    --gold: #e0a91e;
    --white: #f2f2f2;
  }
  * { margin: 0; padding: 0; box-sizing: border-box; }
  html, body { width: 1200px; height: 780px; overflow: hidden; }
  body {
    background: radial-gradient(ellipse at 25% 10%, var(--stage), var(--stage-dark));
    font-family: "Open Sans", Arial, sans-serif;
    position: relative;
  }
  .card {
    position: absolute;
    width: 540px;
    height: 310px;
    background: var(--card);
    border-radius: 24px;
    overflow: hidden;
    box-shadow: 0 18px 40px rgba(0,0,0,.55);
  }
  .card--front { left: 45px; top: 235px; }
  .card--back { left: 615px; top: 235px; }

  .wave { position: absolute; inset: 0; width: 100%; height: 100%; }

  .brand {
    position: absolute;
    display: flex;
    align-items: center;
    gap: 10px;
  }
  .brand__mark { background: var(--red); flex: none; }
  .brand__name {
    color: var(--white);
    font-weight: 700;
    text-transform: uppercase;
    line-height: 1.05;
  }
  .card--front .brand { left: 70px; top: 70px; width: 200px; }
  .card--front .brand__mark { width: 22px; height: 22px; }
  .card--front .brand__name { font-size: 24px; }
  .card--back .brand { left: 130px; top: 110px; width: 300px; justify-content: center; }
  .card--back .brand__mark { width: 32px; height: 32px; }
  .card--back .brand__name { font-size: 34px; }

  .divider {
    position: absolute;
    left: 272px; top: 95px;
    width: 1.5px; height: 140px;
    background: var(--red);
  }
  .contact {
    position: absolute;
    left: 292px; top: 92px;
    color: var(--white);
    font-size: 13px;
    line-height: 1.55;
  }
  .contact__name { color: var(--red); font-weight: 700; font-size: 21px; line-height: 1.15; text-transform: uppercase; }
  .contact__role { margin-bottom: 8px; }
  .contact__row { display: flex; align-items: center; gap: 7px; }
  .contact__row svg { width: 11px; height: 11px; flex: none; }
  .contact__address { margin-top: 4px; }
</style>
</head>
<body>

  <section class="card card--front" aria-label="Business card front">
    <svg class="wave" viewBox="0 0 540 310" preserveAspectRatio="none" aria-hidden="true">
      <path d="M0,95 C55,90 85,160 180,210 C280,262 335,262 372,310 L0,310 Z" fill="var(--red)"/>
      <path d="M0,76 C68,68 98,145 192,194 C292,246 350,252 392,310" fill="none" stroke="var(--gold)" stroke-width="3"/>
    </svg>

    <div class="brand">
      <span class="brand__mark"></span>
      <span class="brand__name">Beacon Alert Group</span>
    </div>

    <div class="divider"></div>

    <div class="contact">
      <p class="contact__name">Daniel Reyes</p>
      <p class="contact__role">Managing Director</p>
      <p class="contact__row">
        <svg viewBox="0 0 24 24"><path fill="var(--red)" d="M6.6 10.8a15.1 15.1 0 0 0 6.6 6.6l2.2-2.2a1 1 0 0 1 1-.25 11.4 11.4 0 0 0 3.6.57 1 1 0 0 1 1 1V20a1 1 0 0 1-1 1A17 17 0 0 1 3 4a1 1 0 0 1 1-1h3.5a1 1 0 0 1 1 1c0 1.25.2 2.45.57 3.57a1 1 0 0 1-.25 1z"/></svg>
        555 204 318
      </p>
      <p class="contact__row">
        <svg viewBox="0 0 24 24"><path fill="var(--red)" d="M2 5h20v14H2z"/><path fill="none" stroke="var(--card)" stroke-width="2" d="M2 6l10 7 10-7"/></svg>
        info@beaconalert.com
      </p>
      <p class="contact__row">
        <svg viewBox="0 0 24 24"><circle cx="12" cy="12" r="10" fill="var(--red)"/><path fill="none" stroke="var(--card)" stroke-width="1.6" d="M2 12h20M12 2c3 3 3 17 0 20M12 2c-3 3-3 17 0 20"/></svg>
        www.beaconalert.com
      </p>
      <p class="contact__address">48 Harbor Road, Easton<br>Ohio, Zip 4302</p>
    </div>
  </section>

  <section class="card card--back" aria-label="Business card back">
    <div class="brand">
      <span class="brand__mark"></span>
      <span class="brand__name">Beacon Alert Group</span>
    </div>
  </section>

</body>
</html>
```